Gestaltung von Honigetiketten
Zielgruppe
Ich bin ein Imker, der im eigenen Restaurant seinen Honig ausstellen und verkaufen möchte.
Aufgabenstellung
Ich möchte exklusive und edle Honigetiketten die auffallen. Bevorzugt mit den Farben Gold und Schwarz, siehe meinem bisher gesehenen Favoriten im Anhang.
Nur das Logo selbst (Baum) soll übernommen werden Farbe kann variieren, ebenso die Schrift ist variabel.
Auf die Vorderseite des Honigetiketts soll zu lesen sein:
- Deutscher Honig
- Sommertracht
- 500g
- Logo und Name
Auf der Rückseite des Honigetiketts soll zu finden sein:
- freies Feld für Stempel für Namen und Adresse des Abfüllers
- freies Feld für das Mindesthaltbarkeitsdatum

```html
<!DOCTYPE html>
<html lang="de">
<head>
<meta charset="utf-8">
<title>Honigetikett – Gasthof zum Ahorn Birkensaal</title>
<link href="https://fonts.googleapis.com/css2?family=Open+Sans:wght@400;600&display=swap" rel="stylesheet">
<style>
  :root {
    --paper: #ffffff;
    --label-black: #0d0d0d;
    --gold: #c9a45a;
    --gold-light: #e8cf8e;
    --gold-dark: #8a6a2c;
    --text-light: #d9d9d9;
    --text-muted: #b8b8b8;
    --field-white: #ffffff;
    --field-red: #d01818;
  }
  * { box-sizing: border-box; margin: 0; padding: 0; }
  html, body { width: 1069px; height: 1200px; overflow: hidden; background: var(--paper); }
  body { font-family: "Open Sans", sans-serif; position: relative; }

  .lid {
    position: absolute; left: 374px; top: 150px; width: 320px; height: 320px; border-radius: 50%;
    background: radial-gradient(circle at 40% 35%, var(--gold-light), var(--gold) 55%, var(--gold-dark));
  }
  .lid-disc {
    position: absolute; left: 37px; top: 37px; width: 246px; height: 246px; border-radius: 50%;
    background: var(--label-black);
  }
  .lid-mark {
    position: absolute; left: 41px; top: 41px; width: 164px; height: 164px; border-radius: 50%;
    border: 3px solid var(--gold);
    display: flex; flex-direction: column; align-items: center; justify-content: center; text-align: center;
    color: var(--gold); font-weight: 600; font-size: 16px; line-height: 1.3;
  }
  .strap {
    position: absolute; left: 502px; top: 440px; width: 64px; height: 262px; background: var(--label-black);
    border-radius: 0 0 4px 4px;
  }

  .front-label {
    position: absolute; left: 270px; top: 700px; width: 527px; height: 234px; background: var(--label-black);
    color: var(--text-light);
  }
  .gold-rule { position: absolute; left: 0; right: 0; height: 3px;
    background: linear-gradient(90deg, var(--gold-dark), var(--gold-light), var(--gold-dark)); }
  .gold-rule.top { top: 9px; }
  .gold-rule.bottom { bottom: 9px; }

  .info-col { position: absolute; left: 22px; top: 34px; width: 118px; text-align: center; font-size: 9px; line-height: 12px; }
  .info-col .origin { font-size: 10px; line-height: 13px; }
  .info-col .variety { color: var(--gold); font-weight: 600; margin-bottom: 5px; }
  .info-col .caption { margin-bottom: 1px; }
  .field {
    background: var(--field-white); color: var(--field-red); font-size: 8.5px; line-height: 12px; font-weight: 600;
    margin: 0 auto 8px; width: 90px;
  }
  .stamp-field {
    position: absolute; left: 15px; top: 152px; width: 130px; height: 50px; background: var(--field-white);
    color: var(--field-red); font-size: 6.5px; font-weight: 600; text-align: center; padding: 10px 6px; line-height: 1.3;
  }

  .bee { position: absolute; left: 146px; top: 88px; width: 34px; height: 34px; border-radius: 50%;
    background: radial-gradient(circle, var(--gold-light), var(--gold-dark)); }
  .hive { position: absolute; left: 344px; top: 82px; width: 30px; height: 50px; border-radius: 45% 45% 20% 20%;
    background: linear-gradient(180deg, var(--gold-light), var(--gold-dark)); }

  .brand-mark {
    position: absolute; left: 186px; top: 26px; width: 152px; text-align: center; color: var(--gold);
  }
  .brand-mark .dot { display: block; width: 104px; height: 104px; margin: 0 auto 12px; border-radius: 50%;
    border: 3px solid var(--gold); }
  .brand-mark .name { font-size: 14px; font-weight: 600; line-height: 1.4; }

  .details-col { position: absolute; left: 382px; top: 30px; width: 132px; text-align: center; font-size: 7.5px; line-height: 1.35; }
  .details-col .storage { margin-bottom: 12px; }
  .details-col .weight { font-size: 17px; color: var(--text-light); margin-bottom: 10px; }
  .details-col .address { color: var(--text-muted); }
  .details-col .contact { display: flex; align-items: center; justify-content: center; gap: 5px; margin-top: 3px; color: var(--text-muted); }
  .details-col svg { display: block; }
</style>
</head>
<body>

<div class="lid" role="img" aria-label="Goldener Deckel mit Wabenmuster">
  <div class="lid-disc">
    <div class="lid-mark">Gasthof zum Ahorn<br>Birkensaal</div>
  </div>
</div>
<div class="strap"></div>

<section class="front-label">
  <div class="gold-rule top"></div>
  <div class="gold-rule bottom"></div>

  <div class="info-col">
    <p class="origin">Deutscher Honig</p>
    <p class="variety">Sommertracht</p>
    <p class="caption">Los Nr.</p>
    <p class="field">AB54893C</p>
    <p class="caption">Mindestens haltbar bis:</p>
    <p class="field">17/11/2020</p>
  </div>
  <div class="stamp-field">freies Feld für Stempel für Namen und Adresse des Abfüllers</div>

  <div class="bee" role="img" aria-label="Goldene Biene"></div>

  <div class="brand-mark">
    <span class="dot"></span>
    <p class="name">Gasthof zum Ahorn<br>Birkensaal</p>
  </div>

  <div class="hive" role="img" aria-label="Goldener Bienenkorb"></div>

  <div class="details-col">
    <p class="storage">Gut verschlossen, kühl, trocken und lichtgeschützt lagern. Kandierter Honig wird durch Erwärmen (Max. 40 Grad C) wieder flüssig und streichfähig.</p>
    <p class="weight">500g Netto</p>
    <svg width="12" height="11" viewBox="0 0 12 11" style="margin:0 auto 2px"><path d="M6 0 L12 5 H10 V11 H2 V5 H0 Z" fill="var(--gold)"/></svg>
    <p class="address">Gasthaus Zum Ahorn-Birkensaal<br>Talweg 12<br>90410 Eichenau</p>
    <p class="contact">
      <svg width="9" height="9" viewBox="0 0 10 10"><circle cx="5" cy="5" r="4.3" fill="none" stroke="var(--gold)"/><path d="M3 3 Q3 7 7 7" stroke="var(--gold)" fill="none" stroke-width="1.4"/></svg>
      01234 / 56 70
    </p>
    <p class="contact">
      <svg width="10" height="8" viewBox="0 0 10 8"><path d="M1 7 H9 L8 4 H2 Z M3 4 Q5 0 7 4" fill="var(--gold)"/></svg>
      01234 / 98 765
    </p>
  </div>
</section>

</body>
</html>
```